Law Firm Business Card

This is a business card for a law firm that serves US military and veterans.

The card must have ONLY the following (we want an uncluttered look):

- Company logo (PNG, GIF, JPEG copies uploaded)
- A tagline reading: "a law firm for service members and veterans"
- My name and title: "Tobias Marlow" and "Attorney"
- My email: "tobias.marlow@brinmoorlegal.com"
- My number: "855-FIRM-ONE (347-6663)"

We are looking for a clean, simple layout with only the above information, likely printed on a bright white cotton stock. The font of our logo is DIN 1451, and the font used on our website is Helvetica Neue. The color of our logo is #336699, and we probably want the tagline in that color also, and my contact information in a dark grey. Please review our website at www.brinmoorlegal.com to ensure your card design complements our website style.

Thanks and we look forward to seeing your submissions.

A few notes:

- Two-sided submissions are ok
- Please don't add graphics (scales of justice, judges hammer, etc)

```html
<!DOCTYPE html>
<html lang="en">
<head>
<meta charset="utf-8">
<title>Brinmoor Legal – Business Card</title>
<link rel="stylesheet" href="https://fonts.googleapis.com/css2?family=Open+Sans:wght@400;700&family=Tinos&display=swap">
<style>
  :root {
    --brand-blue: #2f6bc2;
    --ink-grey: #2b2b2b;
    --rule-grey: #c9cdd3;
    --card-white: #ffffff;
    --stage: #eceef1;
  }
  * { box-sizing: border-box; margin: 0; padding: 0; }
  html, body { width: 1200px; height: 526px; overflow: hidden; }
  body {
    background: var(--stage);
    font-family: "Open Sans", Helvetica, Arial, sans-serif;
    position: relative;
  }
  .card {
    position: absolute;
    top: 113px;
    width: 540px;
    height: 300px;
    border-radius: 30px;
    overflow: hidden;
    box-shadow: 0 6px 18px rgba(0,0,0,0.18);
  }
  .card--front { left: 40px; background: var(--card-white); }
  .card--back { left: 620px; background: var(--brand-blue); }

  .firm-name {
    position: absolute;
    font-family: "Open Sans", Helvetica, Arial, sans-serif;
    font-weight: 700;
    line-height: 1.2;
    text-align: center;
    white-space: nowrap;
  }
  .card--front .firm-name {
    left: 12px; top: 95px; width: 230px;
    font-size: 22px;
    color: var(--brand-blue);
  }
  .card--back .firm-name {
    left: 0; top: 100px; width: 100%;
    font-size: 44px;
    color: var(--card-white);
  }

  .divider {
    position: absolute;
    left: 250px; top: 38px;
    width: 1px; height: 140px;
    background: var(--rule-grey);
  }
  .contact { position: absolute; left: 268px; top: 40px; color: var(--ink-grey); }
  .contact__name { font-size: 20px; font-weight: 700; color: var(--brand-blue); }
  .contact__title { font-size: 14px; margin-top: 2px; }
  .contact__list { list-style: none; margin-top: 22px; }
  .contact__item { display: flex; align-items: center; gap: 8px; font-size: 13px; margin-bottom: 8px; }
  .contact__icon { width: 13px; height: 13px; flex: none; }

  .tagline {
    position: absolute;
    left: 0; width: 100%;
    text-align: center;
    font-family: "Tinos", "Times New Roman", serif;
  }
  .card--front .tagline { top: 203px; font-size: 16px; color: var(--brand-blue); }
  .card--back .tagline { top: 185px; font-size: 21px; color: var(--card-white); }

  .footer-band {
    position: absolute;
    left: 0; bottom: 0;
    width: 100%; height: 62px;
    background: var(--brand-blue);
    color: var(--card-white);
    font-size: 16px;
    display: flex; align-items: center; justify-content: center;
  }
</style>
</head>
<body>
  <section class="card card--front">
    <p class="firm-name">Brinmoor Legal</p>
    <div class="divider"></div>
    <div class="contact">
      <p class="contact__name">Tobias Marlow</p>
      <p class="contact__title">Attorney</p>
      <ul class="contact__list">
        <li class="contact__item">
          <svg class="contact__icon" viewBox="0 0 24 24" aria-hidden="true"><path fill="#2b2b2b" d="M6.6 10.8a15.1 15.1 0 0 0 6.6 6.6l2.2-2.2c.3-.3.7-.4 1-.2 1.1.4 2.3.6 3.6.6.6 0 1 .4 1 1V20c0 .6-.4 1-1 1A17 17 0 0 1 3 4c0-.6.4-1 1-1h3.5c.6 0 1 .4 1 1 0 1.3.2 2.5.6 3.6.1.3 0 .7-.2 1z"/></svg>
          <span>855-FIRM-ONE (347-6663)</span>
        </li>
        <li class="contact__item">
          <svg class="contact__icon" viewBox="0 0 24 24" aria-hidden="true"><rect x="2" y="5" width="20" height="14" rx="2" fill="#2b2b2b"/><path d="M3 6l9 7 9-7" fill="none" stroke="#fff" stroke-width="1.6"/></svg>
          <span>tobias.marlow@brinmoorlegal.com</span>
        </li>
      </ul>
    </div>
    <p class="tagline">A Law Firm For Service Members &amp; Veterans</p>
    <div class="footer-band">www.brinmoorlegal.com</div>
  </section>

  <section class="card card--back">
    <p class="firm-name">Brinmoor Legal</p>
    <p class="tagline">A Law Firm For Service Members &amp; Veterans</p>
  </section>
</body>
</html>
```